Velmora Freightway Solutions Business cards

Would like a very unique design catchy but professional for business cards. Please use log provided.Marlon WellsCeo and Founder TransCon Logistix Solutions1-888-913-3225mwells@tlsolutionsus.comwww.tlsolutionsus.com

```html
<!DOCTYPE html>
<html lang="en">
<head>
<meta charset="utf-8">
<title>Velmora Freightway Solutions – Business Cards</title>
<link href="https://fonts.googleapis.com/css2?family=Montserrat:wght@300;400;600;700&family=Open+Sans:wght@400&display=swap" rel="stylesheet">
<style>
  :root {
    --backdrop: #2b2b2b;
    --card: #171717;
    --brand-blue: #1f78cc;
    --brand-red: #e0242b;
    --ink: #f2f2f2;
  }
  * { margin: 0; padding: 0; box-sizing: border-box; }
  html, body { width: 1200px; height: 900px; overflow: hidden; background: var(--backdrop); }
  .canvas { position: relative; width: 1200px; height: 900px; }
  .card {
    position: absolute; width: 600px; height: 343px;
    background: var(--card);
    box-shadow: 0 18px 40px rgba(0,0,0,.45);
  }
  .card--front { left: 470px; top: 80px; }
  .card--back { left: 130px; top: 475px; }

  .brand {
    display: flex; align-items: center; gap: 12px;
    font-family: "Montserrat", sans-serif; font-weight: 700;
    color: var(--brand-blue); text-transform: uppercase; letter-spacing: 1px;
  }
  .brand__square { width: 16px; height: 16px; background: var(--brand-red); flex: none; }

  .card--front .brand { position: absolute; left: 0; right: 0; top: 130px; justify-content: center; font-size: 25px; }
  .card--front .site {
    position: absolute; left: 0; right: 0; top: 200px; text-align: center;
    font-family: "Open Sans", sans-serif; font-size: 14px; letter-spacing: 2px;
    color: var(--brand-blue);
  }

  .person { position: absolute; left: 40px; top: 36px; font-family: "Montserrat", sans-serif; }
  .person__name { font-size: 21px; color: var(--ink); font-weight: 300; text-transform: uppercase; letter-spacing: .5px; }
  .person__name strong { font-weight: 700; }
  .person__title { margin-top: 4px; font-size: 13px; color: var(--brand-red); text-transform: uppercase; font-weight: 400; }
  .person__rule { margin-top: 8px; width: 70px; height: 3px; background: var(--brand-blue); }

  .card--back .brand { position: absolute; right: 36px; top: 120px; font-size: 16px; gap: 9px; }
  .card--back .brand__square { width: 11px; height: 11px; }

  .contact { position: absolute; left: 40px; top: 208px; font-family: "Open Sans", sans-serif; color: var(--ink); font-size: 15px; list-style: none; }
  .contact li { display: flex; align-items: center; gap: 10px; height: 24px; }
  .contact svg { width: 14px; height: 14px; fill: var(--brand-red); flex: none; }
  .contact .address { margin-top: 4px; font-size: 16px; }
</style>
</head>
<body>
<div class="canvas">

  <section class="card card--front">
    <div class="brand"><span class="brand__square"></span>Velmora Freightway Solutions</div>
    <p class="site">www.vfwayroutes.com</p>
  </section>

  <section class="card card--back">
    <div class="person">
      <p class="person__name">Dorian <strong>Pike</strong></p>
      <p class="person__title">CEO and Founder</p>
      <div class="person__rule"></div>
    </div>

    <div class="brand"><span class="brand__square"></span>Velmora Freightway Solutions</div>

    <ul class="contact">
      <li>
        <svg viewBox="0 0 16 16" aria-hidden="true"><path d="M2 5c0-2 2-3 6-3s6 1 6 3v1h-3V5H5v1H2zM4 7h8l2 6H2z"/></svg>
        1-888-470-6158
      </li>
      <li>
        <svg viewBox="0 0 16 16" aria-hidden="true"><path d="M1 3h14v10H1zM2.5 4.5 8 9l5.5-4.5" stroke="#171717" stroke-width="1.2"/></svg>
        dpike@vfwayroutes.com
      </li>
      <li>
        <svg viewBox="0 0 16 16" aria-hidden="true"><circle cx="8" cy="8" r="7"/><path d="M1 8h14M8 1c-3 3-3 11 0 14M8 1c3 3 3 11 0 14" stroke="#171717" stroke-width="1" fill="none"/></svg>
        www.vfwayroutes.com
      </li>
      <li class="address">2417 Calder Mill Rd, Atlanta, GA 30327</li>
    </ul>
  </section>

</div>
</body>
</html>
```